Local Flower Farm Needs Business Card Design

I need business cards designed for a flower farm based in Eudora, Kansas.
Business Info:
We are a local cut flower farm located in Eudora, Kansas, founded by Corinne Haldwick. What started as a passion for agriculture and search for more joy in daily life has blossomed into a small business dedicated to providing the community with beautiful, fresh, and sustainable flowers. We specialize in local, seasonal blooms, ensuring that every petal reflects the care and dedication we pour into our craft. Our mission is to deliver the highest quality flowers directly to our customers through local farmers markets and to florists who share our commitment to sustainability. Join us in celebrating the beauty of nature, one bloom at a time!
Contact Details:
Corinne Haldwick
Owner
Phone 913-555-0147
Facebook: Rosalind Thorpe Gardens
Instagram: @RosalindThorpeGardens
Website: RosalindThorpeGardens.example
Target Market(s)
Wholesale to Florists and Direct to Consumer via Farmers Market
Industry/Entity Type
Florist, Farm
Contact Information for Business Card
Name, Contact Info, Logo
Look and feel
Each slider illustrates characteristics of the customer's brand and the style your logo design should communicate.

```html
<!DOCTYPE html>
<html lang="en">
<head>
<meta charset="utf-8">
<title>Rosalind Thorpe Gardens — Business Card</title>
<link rel="stylesheet" href="https://fonts.googleapis.com/css2?family=EB+Garamond:wght@400;500&display=swap">
<style>
  :root {
    --backdrop: #2b2b2d;
    --card-dark: #0b2a30;
    --card-light: #ffffff;
    --ink-dark: #0f2a30;
    --ink-light: #f4f1ea;
    --rule-light: rgba(244, 241, 234, 0.85);
  }
  * { box-sizing: border-box; margin: 0; padding: 0; }
  html, body {
    width: 1200px; height: 1200px; overflow: hidden;
    background: var(--backdrop);
    font-family: "EB Garamond", Georgia, serif;
  }
  .sheet {
    width: 1200px; height: 1200px;
    display: flex; flex-direction: column;
    align-items: center; justify-content: center; gap: 44px;
  }
  .card {
    width: 860px; height: 491px;
    position: relative;
    box-shadow: 0 14px 30px rgba(0,0,0,0.45);
  }
  .card--front { background: var(--card-dark); color: var(--ink-light); }
  .card--back { background: var(--card-light); color: var(--ink-dark); }

  .brand-seal {
    position: absolute; left: 50%; top: 56px;
    transform: translateX(-50%);
    width: 290px; height: 290px;
    border: 1.5px solid var(--rule-light);
    border-radius: 50%;
    display: flex; align-items: center; justify-content: center;
    text-align: center;
  }
  .brand-name {
    font-size: 30px; font-weight: 400; line-height: 1.25;
    letter-spacing: 0.12em; text-transform: uppercase;
    color: var(--ink-light);
  }
  .front-url {
    position: absolute; left: 0; right: 0; bottom: 58px;
    text-align: center;
    font-size: 21px; letter-spacing: 0.32em; text-transform: uppercase;
  }

  .identity {
    position: absolute; right: 476px; top: 178px;
    text-align: right;
  }
  .person-name {
    font-size: 34px; font-weight: 400; letter-spacing: 0.08em;
    text-transform: uppercase; line-height: 1.1;
  }
  .person-role { font-size: 22px; letter-spacing: 0.06em; margin-top: 4px; }
  .divider {
    position: absolute; left: 408px; top: 160px;
    width: 2px; height: 166px; background: var(--ink-dark);
  }
  .contact-list {
    position: absolute; left: 440px; top: 164px;
    list-style: none;
  }
  .contact-item {
    display: flex; align-items: center; gap: 12px;
    font-size: 25px; line-height: 38px;
  }
  .contact-icon { width: 24px; height: 24px; flex: none; }
</style>
</head>
<body>
<main class="sheet">
  <section class="card card--front">
    <div class="brand-seal">
      <p class="brand-name">Rosalind<br>Thorpe<br>Gardens</p>
    </div>
    <p class="front-url">www.rosalindthorpegardens.example</p>
  </section>

  <section class="card card--back">
    <div class="identity">
      <h1 class="person-name">Corinne Haldwick</h1>
      <p class="person-role">Owner</p>
    </div>
    <div class="divider"></div>
    <ul class="contact-list">
      <li class="contact-item">
        <svg class="contact-icon" viewBox="0 0 24 24" aria-hidden="true">
          <circle cx="12" cy="12" r="10.5" fill="none" stroke="#0f2a30" stroke-width="1.5"/>
          <path d="M9 6.5c-1 .4-1.6 1.3-1.4 2.6.5 3.3 3.8 7.2 7 8.3 1.2.4 2.2 0 2.7-.9l-2-1.8-1.3.8c-1.4-.8-2.9-2.6-3.5-4.2l1.1-1z" fill="#0f2a30"/>
        </svg>
        <span>913-555-0147</span>
      </li>
      <li class="contact-item">
        <svg class="contact-icon" viewBox="0 0 24 24" aria-hidden="true"><circle cx="12" cy="12" r="10.5" fill="none" stroke="#0f2a30" stroke-width="1.5"/></svg>
        <span>Rosalind Thorpe Gardens</span>
      </li>
      <li class="contact-item">
        <svg class="contact-icon" viewBox="0 0 24 24" aria-hidden="true"><circle cx="12" cy="12" r="10.5" fill="none" stroke="#0f2a30" stroke-width="1.5"/></svg>
        <span>@RosalindThorpeGardens</span>
      </li>
      <li class="contact-item">
        <svg class="contact-icon" viewBox="0 0 24 24" aria-hidden="true">
          <circle cx="12" cy="12" r="10.5" fill="none" stroke="#0f2a30" stroke-width="1.5"/>
          <ellipse cx="12" cy="12" rx="4.5" ry="10.5" fill="none" stroke="#0f2a30" stroke-width="1.2"/>
          <line x1="1.5" y1="12" x2="22.5" y2="12" stroke="#0f2a30" stroke-width="1.2"/>
        </svg>
        <span>RosalindThorpeGardens.example</span>
      </li>
    </ul>
  </section>
</main>
</body>
</html>
```